Business Card Design Project

This is the first time we use our new logo. We need a business card that we can use both on our institutional corporate relationships and also that works for our staff that deals with consumers directly.

VELUNDA is a new company dedicated to empower consumers and to provide them with the best choices for specialized health care using the latest telemedicine technology (medicine at a distance via videoconference).

We want to print this cards in high quality materials and process. We will like designs that allow us to use UV spot varnish and other techniques that will differentiate us.

We are including Two different versions of Color logos. In addition we are including white over black background logos. Those can be used replacing the black for a color.

Please note this is the first time we will be creating any corporate materials with our new logo and colors.

Target Market(s)

34+ consumers of medium high and high socioeconomic levels.

Industry/Entity Type

Health

Requirements
Must have
• Our logo on its original colors
Should not have
• Any other graphical element or design that is not our logo

```html
<!DOCTYPE html>
<html lang="en">
<head>
<meta charset="utf-8">
<title>VELUNDA — Business Card</title>
<link rel="stylesheet" href="https://fonts.googleapis.com/css2?family=Montserrat:wght@700&family=Arimo:wght@400&display=swap">
<style>
  :root {
    --page: #e9e6e2;
    --card-white: #ffffff;
    --brand-blue: #1b5681;
    --ink: #222a30;
    --teal: #1fa89a;
    --icon: #2f5f8f;
    --faint: #e4f0f5;
  }
  * { margin: 0; padding: 0; box-sizing: border-box; }
  html, body { width: 1200px; height: 1057px; overflow: hidden; background: var(--page); }
  .canvas { position: relative; width: 1200px; height: 1057px; }

  .card {
    position: absolute;
    left: 190px;
    width: 820px;
    height: 468px;
    box-shadow: 0 6px 18px rgba(0,0,0,0.18);
  }
  .card--front { top: 40px; background: var(--card-white); }
  .card--back { top: 549px; background: var(--brand-blue); }

  /* Front */
  .brand {
    position: absolute; left: 60px; top: 120px;
    display: flex; align-items: center; gap: 22px;
  }
  .brand__dot { width: 64px; height: 64px; border-radius: 50%; background: var(--brand-blue); }
  .brand__name {
    font-family: "Montserrat", sans-serif; font-weight: 700;
    font-size: 62px; letter-spacing: 5px; color: var(--brand-blue);
  }
  .faint-circle {
    position: absolute; right: 40px; top: 40px;
    width: 200px; height: 200px; border-radius: 50%; background: var(--faint);
  }
  .person { position: absolute; right: 70px; top: 90px; text-align: right; }
  .person__name {
    font-family: "Montserrat", sans-serif; font-weight: 700;
    font-size: 30px; color: var(--brand-blue);
  }
  .person__title {
    font-family: "Arimo", sans-serif; font-size: 22px; color: var(--teal); margin-top: 2px;
  }
  .contacts {
    position: absolute; left: 60px; top: 258px; list-style: none;
    font-family: "Arimo", sans-serif; font-size: 21px; color: var(--ink);
  }
  .contacts li { display: flex; align-items: center; gap: 12px; height: 31px; }
  .contacts svg { width: 18px; height: 18px; flex: none; }
  .address {
    position: absolute; left: 60px; top: 398px;
    font-family: "Arimo", sans-serif; font-size: 21px; color: var(--ink);
  }

  /* Back */
  .back-mark {
    position: absolute; left: 0; right: 0; top: 120px;
    display: flex; flex-direction: column; align-items: center; gap: 26px;
  }
  .back-mark__dot { width: 120px; height: 120px; border-radius: 50%; background: var(--card-white); }
  .back-mark__name {
    font-family: "Montserrat", sans-serif; font-weight: 700;
    font-size: 52px; letter-spacing: 6px; color: var(--card-white);
  }
  .back-url {
    position: absolute; left: 0; right: 0; bottom: 46px; text-align: center;
    font-family: "Arimo", sans-serif; font-size: 26px; letter-spacing: 7px; color: var(--card-white);
  }
</style>
</head>
<body>
<main class="canvas">
  <section class="card card--front" aria-label="Card front">
    <div class="faint-circle"></div>
    <div class="brand">
      <span class="brand__dot"></span>
      <span class="brand__name">VELUNDA</span>
    </div>
    <div class="person">
      <p class="person__name">Your Name</p>
      <p class="person__title">Title</p>
    </div>
    <ul class="contacts">
      <li>
        <svg viewBox="0 0 20 20"><circle cx="10" cy="10" r="8.5" fill="none" stroke="var(--icon)" stroke-width="1.6"/><path d="M7 5.5c-1 1 -1 4 1.5 6.5s5.5 2.5 6.5 1.5l-1.8-1.8-1.5 1c-1-.4-2.6-2-3-3l1-1.5z" fill="var(--icon)"/></svg>
        012-555-0147
      </li>
      <li>
        <svg viewBox="0 0 20 20"><circle cx="10" cy="10" r="8.5" fill="none" stroke="var(--icon)" stroke-width="1.6"/><path d="M7 5.5c-1 1 -1 4 1.5 6.5s5.5 2.5 6.5 1.5l-1.8-1.8-1.5 1c-1-.4-2.6-2-3-3l1-1.5z" fill="var(--icon)"/></svg>
        012-555-0147
      </li>
      <li>
        <svg viewBox="0 0 20 20"><rect x="2" y="5" width="16" height="11" rx="1" fill="var(--icon)"/><path d="M2.5 5.5 10 11l7.5-5.5" fill="none" stroke="#fff" stroke-width="1.4"/></svg>
        name@velunda.com
      </li>
      <li>
        <svg viewBox="0 0 20 20"><circle cx="10" cy="10" r="8" fill="none" stroke="var(--icon)" stroke-width="1.6"/><ellipse cx="10" cy="10" rx="3.5" ry="8" fill="none" stroke="var(--icon)" stroke-width="1.2"/><path d="M2 10h16M3.5 6h13M3.5 14h13" stroke="var(--icon)" stroke-width="1.2"/></svg>
        www.velunda.com
      </li>
    </ul>
    <p class="address">Street Name, City Name, State, City Zip Code</p>
  </section>

  <section class="card card--back" aria-label="Card back">
    <div class="back-mark">
      <span class="back-mark__dot"></span>
      <span class="back-mark__name">VELUNDA</span>
    </div>
    <p class="back-url">www.velunda.com</p>
  </section>
</main>
</body>
</html>
```